we can communicate on this, but i want to follow the approach we took on Pellew|Marsh & Quinlan but i feel the card front needs the black background and the platinum and gold logo. The back? I am open. we can use the same info from PM&Q. Velmont Arc is an enhanced equity investment fund - basically a very exclusive boutique hedge fund that uses only stock options. very advanced things. hope you are interested

Contact Information for Business Card

Dr. Lewis T. Brennick, CFA
Scientifique de fusée financière
701.555.0143
LTBquant47@mailvantor.com

4718 Willow Creek Bend W.
West Fargo, ND 58078

No web site

Colors

Designer to choose colors to be used in the design.

Requirements
Nice to have
• I tend to prefer the most visible applications of the logo to include logo and name, the logo version with a black background and the gold and platinum components separated by the black. I see this working well for a single side (logo and name - this is card front to me).
• I am fairly open to other treatments on the reverse side with the data. To me, it makes sense to have a different color rendition of the logo on the reverse and it may be a muted black tone on tone or an oversized portion that would have spot UV. Or, the reverse may play with colors and layout
Should not have
• Other colors = no no
• Decorative font

```html
<!DOCTYPE html>
<html lang="en">
<head>
<meta charset="utf-8">
<title>Velmont Arc — Business Card</title>
<link rel="stylesheet" href="https://fonts.googleapis.com/css2?family=Montserrat:wght@400;700&family=Roboto:wght@400;500&display=swap">
<style>
  :root {
    --backdrop: #3b3b3d;
    --card: #1c1c1e;
    --white: #f4f4f4;
    --gold: #d9b53c;
    --gold-light: #efe06a;
    --gold-dark: #a88a1f;
    --platinum: #c9c9cc;
    --platinum-dark: #6b6b70;
  }
  * { box-sizing: border-box; margin: 0; padding: 0; }
  html, body { width: 799px; height: 1200px; overflow: hidden; }
  body {
    background: var(--backdrop);
    font-family: "Roboto", Arial, sans-serif;
    position: relative;
  }
  .card {
    position: absolute;
    left: 80px;
    width: 640px;
    height: 366px;
    background: var(--card);
    border-radius: 4px;
    box-shadow: 0 14px 30px rgba(0,0,0,.45);
    overflow: hidden;
  }
  .card--front { top: 150px; }
  .card--back { top: 690px; }

  /* front: gold mark with platinum name */
  .front-mark {
    position: absolute;
    left: 50%;
    top: 70px;
    transform: translateX(-50%);
    display: flex;
    flex-direction: column;
    align-items: center;
    gap: 22px;
  }
  .front-mark__circle {
    width: 130px; height: 130px;
    border-radius: 50%;
    background: linear-gradient(135deg, var(--gold-light), var(--gold-dark));
  }
  .front-mark__name {
    font-family: "Montserrat", Arial, sans-serif;
    font-weight: 700;
    font-size: 46px;
    letter-spacing: 1px;
    color: var(--platinum);
    text-transform: uppercase;
    white-space: nowrap;
  }

  /* back */
  .back-mark {
    position: absolute;
    left: 36px;
    top: 92px;
    display: flex;
    flex-direction: column;
    align-items: center;
    gap: 16px;
  }
  .back-mark__circle {
    width: 92px; height: 92px;
    border-radius: 50%;
    background: linear-gradient(135deg, var(--gold-light), var(--gold-dark));
  }
  .back-mark__name {
    font-family: "Montserrat", Arial, sans-serif;
    font-weight: 700;
    font-size: 32px;
    letter-spacing: .5px;
    color: var(--white);
    text-transform: uppercase;
    white-space: nowrap;
  }
  .contact {
    position: absolute;
    left: 358px;
    top: 104px;
    width: 266px;
    color: var(--white);
    font-size: 14px;
    line-height: 1.45;
  }
  .contact__name {
    color: var(--gold);
    font-weight: 500;
    font-size: 18px;
    white-space: nowrap;
  }
  .contact__role { font-size: 14px; margin-bottom: 12px; white-space: nowrap; }
  .contact__row { display: flex; align-items: center; gap: 10px; white-space: nowrap; }
  .contact__row svg { width: 13px; height: 13px; flex: none; fill: var(--gold); }
  .contact__address { margin-top: 4px; }

  .strip-platinum {
    position: absolute;
    left: 0; bottom: 58px;
    width: 300px; height: 12px;
    background: linear-gradient(90deg, var(--platinum-dark), var(--platinum) 40%, var(--platinum-dark));
  }
  .band-gold {
    position: absolute;
    right: 0; bottom: 0;
    width: 370px; height: 70px;
    border-top-left-radius: 22px;
    background: linear-gradient(90deg, var(--gold-dark), var(--gold-light) 45%, var(--gold-dark));
  }
</style>
</head>
<body>
  <section class="card card--front" aria-label="Card front">
    <div class="front-mark">
      <div class="front-mark__circle"></div>
      <div class="front-mark__name">Velmont Arc</div>
    </div>
  </section>

  <section class="card card--back" aria-label="Card back">
    <div class="back-mark">
      <div class="back-mark__circle"></div>
      <div class="back-mark__name">Velmont Arc</div>
    </div>

    <div class="contact">
      <div class="contact__name">Dr. Lewis T. Brennick, CFA</div>
      <div class="contact__role">Scientifique de fusée financière</div>
      <div class="contact__row">
        <svg viewBox="0 0 24 24" aria-hidden="true"><path d="M6.6 10.8a15.1 15.1 0 0 0 6.6 6.6l2.2-2.2a1 1 0 0 1 1-.25 11.4 11.4 0 0 0 3.6.57 1 1 0 0 1 1 1V20a1 1 0 0 1-1 1A17 17 0 0 1 3 4a1 1 0 0 1 1-1h3.5a1 1 0 0 1 1 1c0 1.25.2 2.45.57 3.6a1 1 0 0 1-.25 1z"/></svg>
        <span>701.555.0143</span>
      </div>
      <div class="contact__row">
        <svg viewBox="0 0 24 24" aria-hidden="true"><path d="M2 5h20v14H2zM3.5 6.5 12 13l8.5-6.5z" fill-rule="evenodd"/></svg>
        <span>LTBquant47@mailvantor.com</span>
      </div>
      <div class="contact__address">4718 Willow Creek Bend W.<br>West Fargo, ND 58078</div>
    </div>

    <div class="strip-platinum"></div>
    <div class="band-gold"></div>
  </section>
</body>
</html>
```